Business card design needed

OH&S consultancy and training

Industry/Entity Type

Training

Contact Information for Business Card

Coastal Hazard & Learning Collective
Dorian Whitfield
Director

0427 913 058
dorian.whitfield@chlcollect.com.au
chlcollect.com.au

Ph: 03 9172 4039
Fx: 03 9172 4041

```html
<!DOCTYPE html>
<html lang="en">
<head>
<meta charset="utf-8">
<title>Coastal Hazard &amp; Learning Collective – Business Card</title>
<link rel="stylesheet" href="https://fonts.googleapis.com/css2?family=Barlow:wght@400;500;600&display=swap">
<style>
  :root {
    --stage: #dfe3e6;
    --paper: #ffffff;
    --charcoal: #4b4c4e;
    --charcoal-dark: #3f4042;
    --band-grey: #5d5e60;
    --signal-yellow: #f6e500;
    --ink: #2d2e30;
    --logo-grey: #a9aaac;
    --text-font: "Barlow", Arial, sans-serif;
  }
  * { box-sizing: border-box; margin: 0; padding: 0; }
  html, body {
    width: 1200px; height: 960px; overflow: hidden;
    background: var(--stage);
    font-family: var(--text-font);
  }
  .canvas { position: relative; width: 1200px; height: 960px; }

  .card {
    position: absolute; left: 300px; width: 600px; height: 340px;
    overflow: hidden; border-radius: 3px;
    box-shadow: 0 10px 28px rgba(0,0,0,.18);
  }

  /* Front */
  .card-front { top: 100px; background: var(--paper); color: var(--ink); }
  .brand {
    position: absolute; display: flex; align-items: center; gap: 12px;
    font-weight: 500;
  }
  .brand-mark { width: 16px; height: 16px; background: var(--signal-yellow); flex: none; }
  .card-front .brand { left: 44px; top: 44px; font-size: 24px; color: var(--logo-grey); }

  .person { position: absolute; right: 282px; top: 132px; text-align: right; }
  .person-name { font-size: 30px; font-weight: 400; letter-spacing: .5px; }
  .person-role { font-size: 18px; margin-top: 4px; }
  .person-mobile { font-size: 18px; margin-top: 22px; letter-spacing: .5px; }
  .person-email {
    position: absolute; left: 32px; top: 262px; font-size: 18px; letter-spacing: .4px;
  }

  .office { position: absolute; left: 380px; top: 178px; font-size: 17px; line-height: 25px; }
  .office-line { display: flex; gap: 12px; letter-spacing: .5px; }
  .office-label { color: var(--signal-yellow); font-weight: 600; width: 12px; }
  .office-web { font-weight: 600; }

  .stripe-yellow { position: absolute; left: 0; right: 0; top: 298px; height: 9px; background: var(--signal-yellow); }
  .stripe-grey { position: absolute; left: 0; right: 0; top: 307px; bottom: 0; background: var(--band-grey); }

  /* Back */
  .card-back {
    top: 500px;
    background: linear-gradient(135deg, var(--charcoal) 0%, var(--charcoal-dark) 100%);
  }
  .card-back .brand {
    left: 0; right: 0; top: 128px; justify-content: center;
    font-size: 30px; color: #d6d7d9;
  }
  .card-back .brand-mark { width: 20px; height: 20px; }
  .web-tab {
    position: absolute; left: 150px; width: 300px; bottom: 0; height: 34px;
    background: var(--signal-yellow); border-radius: 12px 12px 0 0;
    display: flex; align-items: center; justify-content: center;
    font-size: 17px; font-weight: 600; letter-spacing: 1px; color: var(--ink);
  }
</style>
</head>
<body>
<main class="canvas">
  <section class="card card-front">
    <div class="brand"><span class="brand-mark"></span>Coastal Hazard &amp; Learning Collective</div>
    <div class="person">
      <p class="person-name">Dorian Whitfield</p>
      <p class="person-role">Director</p>
      <p class="person-mobile">0427 913 058</p>
    </div>
    <p class="person-email">dorian.whitfield@chlcollect.com.au</p>
    <div class="office">
      <p class="office-line"><span class="office-label">T</span>03 9172 4039</p>
      <p class="office-line"><span class="office-label">F</span>03 9172 4041</p>
      <p class="office-web">chlcollect.com.au</p>
    </div>
    <div class="stripe-yellow"></div>
    <div class="stripe-grey"></div>
  </section>

  <section class="card card-back">
    <div class="brand"><span class="brand-mark"></span>Coastal Hazard &amp; Learning Collective</div>
    <div class="web-tab">chlcollect.com.au</div>
  </section>
</main>
</body>
</html>
```